Marlow Estate Fixers (Handyman / Home Improvement Company)

Looking for a double sided professional looking business card with Logo attached to be highlighted on one side and throwing in an image of a handyman as an option would be nice to see as well. We are a company focused on providing quality Handyman and Home improvement services in a timely manner that is done right the first time with integrity

Industry/Entity Type

Handyman / Home Improvement

Contact Information for Business Card

(LOGO, Name, Mobile and office phone numbers, email) on front side of card, (the words "The SOLUTION to all of your Handyman and Home Improvement needs" followed by "Family Owned and Operated" at the very bottom) on the back.

Colors
EB3D1F
EC4F4E
F09395
F8D3D4
FCEDEE

Requirements
Must have
• Red, Gray, Black Color scheme
Should not have
• No Yellow or Blue colors

```html
<!DOCTYPE html>
<html lang="en">
<head>
<meta charset="utf-8">
<title>Marlow Estate Fixers – Business Card</title>
<link rel="stylesheet" href="https://fonts.googleapis.com/css2?family=Montserrat:wght@400;500;700;800&display=swap">
<style>
  :root {
    --stage: #2a2a2b;
    --card: #1c1c1d;
    --card-edge: #262627;
    --emboss: #0e0e0f;
    --muted: #6a6a6c;
    --red: #eb3d1f;
    --white: #ffffff;
    --soft: #d9d9d9;
  }
  * { box-sizing: border-box; margin: 0; padding: 0; }
  html, body { width: 1200px; height: 875px; overflow: hidden; }
  body {
    background: var(--stage);
    font-family: "Montserrat", sans-serif;
    display: flex;
    align-items: center;
    justify-content: center;
    gap: 60px;
  }
  .card {
    width: 520px;
    height: 300px;
    background: var(--card);
    border: 1px solid var(--card-edge);
    border-radius: 18px;
    position: relative;
    overflow: hidden;
  }
  .brand {
    display: flex;
    align-items: center;
    justify-content: center;
    gap: 12px;
    white-space: nowrap;
  }
  .brand__dot { width: 20px; height: 20px; border-radius: 50%; flex: none; }
  .brand__name {
    font-weight: 800;
    letter-spacing: 1px;
    text-transform: uppercase;
    line-height: 1.1;
  }

  /* back side */
  .card--back {
    display: flex;
    flex-direction: column;
    align-items: center;
    padding: 0 40px;
  }
  .card--back .brand { margin-top: 92px; }
  .card--back .brand__dot { background: var(--emboss); }
  .card--back .brand__name { color: var(--emboss); font-size: 28px; }
  .tagline {
    margin-top: 22px;
    max-width: 380px;
    text-align: center;
    font-size: 14px;
    font-weight: 500;
    line-height: 1.45;
    color: var(--soft);
  }
  .tagline strong { color: var(--red); font-weight: 700; }
  .family {
    position: absolute; left: 0; right: 0; bottom: 22px;
    text-align: center;
    font-size: 12px;
    font-weight: 700;
    letter-spacing: 2px;
    text-transform: uppercase;
    color: var(--muted);
  }

  /* front side */
  .card--front .brand { position: absolute; left: 0; right: 0; top: 52px; }
  .card--front .brand__dot { background: var(--red); }
  .card--front .brand__name { color: var(--white); font-size: 22px; }

  .details {
    position: absolute; left: 0; right: 0; top: 120px;
    display: flex; align-items: center; justify-content: center; gap: 20px;
  }
  .person { text-align: right; white-space: nowrap; }
  .person__name { font-size: 22px; font-weight: 800; color: var(--white); }
  .person__name .surname { color: var(--red); }
  .person__role { font-size: 13px; font-weight: 500; color: var(--soft); margin-top: 2px; }
  .divider { width: 2px; height: 70px; background: var(--red); flex: none; }
  .contacts { list-style: none; display: grid; gap: 7px; }
  .contacts li {
    display: flex; align-items: center; gap: 9px;
    font-size: 13px; color: var(--white); white-space: nowrap;
  }
  .contacts svg { width: 13px; height: 13px; fill: var(--red); flex: none; }
  .address {
    position: absolute; left: 0; right: 0; top: 236px;
    text-align: center; font-size: 13px; color: var(--white); letter-spacing: .3px;
  }
</style>
</head>
<body>
  <section class="card card--back" aria-label="Card back">
    <div class="brand">
      <span class="brand__dot"></span>
      <span class="brand__name">Marlow Estate Fixers</span>
    </div>
    <p class="tagline">The <strong>SOLUTION</strong> to all of your Handyman and Home Improvement needs</p>
    <p class="family">Family Owned and Operated</p>
  </section>

  <section class="card card--front" aria-label="Card front">
    <div class="brand">
      <span class="brand__dot"></span>
      <span class="brand__name">Marlow Estate Fixers</span>
    </div>

    <div class="details">
      <div class="person">
        <p class="person__name">Dana <span class="surname">Whitfield</span></p>
        <p class="person__role">Managing Director</p>
      </div>
      <span class="divider"></span>
      <ul class="contacts">
        <li>
          <svg viewBox="0 0 24 24"><path d="M6.6 10.8a15 15 0 0 0 6.6 6.6l2.2-2.2a1 1 0 0 1 1-.25 11.4 11.4 0 0 0 3.6.6 1 1 0 0 1 1 1V20a1 1 0 0 1-1 1A17 17 0 0 1 3 4a1 1 0 0 1 1-1h3.5a1 1 0 0 1 1 1c0 1.25.2 2.45.6 3.6a1 1 0 0 1-.25 1z"/></svg>
          (08) 4410 2738
        </li>
        <li>
          <svg viewBox="0 0 24 24"><path d="M2 5h20v14H2zm2 2v.5l8 5 8-5V7l-8 5z"/></svg>
          hello@marlowfixers.com
        </li>
        <li>
          <svg viewBox="0 0 24 24"><circle cx="12" cy="12" r="10"/></svg>
          www.marlowfixers.com
        </li>
      </ul>
    </div>

    <p class="address">48 Harbour Lane, Easton, USA</p>
  </section>
</body>
</html>
```